Mobile welding fabrication and repair, heavy equipment and semi repair

We need a business card design that will catch the eye but look prelesional at the same time. Were based out of Idaho and we do all welding fabrication jobs and repairs, we also build and install custom pipe fences for personal or larger scale fence jobs and can give free quotes. We can do semi truck and trailer repairs Mobily also.

Target Market(s)

Welding

Industry/Entity Type

welding and repair

Contact Information for Business Card

email (ravenforgeandmend@mailbay.net, phone number 208-417-3826, owner (Dalton Whitcomb), Pipe Fence, Semi Repair, Mobile welding and fabrication

Font styles to use
Sans Serif

Requirements
Must have
• My logo in black background on one side , and other side my logo in white back round with all the information listed on card details
Nice to have
• make it stand out from other business cards

```html
<!DOCTYPE html>
<html lang="en">
<head>
<meta charset="utf-8">
<title>Raven Forge and Mend – Business Card</title>
<link href="https://fonts.googleapis.com/css2?family=Lato:wght@400;700;900&display=swap" rel="stylesheet">
<style>
  :root {
    --page-bg: #a9a9a9;
    --brand-blue: #0a7fcb;
    --brand-blue-deep: #0456b0;
    --brand-blue-light: #0b95d6;
    --ink: #2a2a2a;
    --rule: #b8b8b8;
    --card-white: #ffffff;
  }
  * { margin: 0; padding: 0; box-sizing: border-box; }
  html, body {
    width: 1200px; height: 1200px; overflow: hidden;
    background: var(--page-bg);
    font-family: "Lato", sans-serif;
  }
  .stage { position: relative; width: 1200px; height: 1200px; }
  .card {
    position: absolute; top: 303px; width: 368px; height: 594px;
    box-shadow: 3px 4px 6px rgba(0,0,0,0.45);
  }
  .card--front {
    left: 201px;
    background: linear-gradient(180deg, var(--brand-blue-light) 0%, var(--brand-blue) 45%, var(--brand-blue-deep) 100%);
  }
  .card--front .pattern {
    position: absolute; inset: 0;
    background: radial-gradient(ellipse at 50% 55%, rgba(255,255,255,0.06), rgba(0,0,0,0.05) 70%);
  }
  .card--back {
    left: 600px; background: var(--card-white);
    text-align: center; color: var(--ink);
  }
  .wordmark {
    font-weight: 900; text-transform: uppercase; letter-spacing: 1px;
    line-height: 1.05;
  }
  .card--front .wordmark {
    position: absolute; left: 0; right: 0; top: 250px;
    color: var(--card-white); font-size: 38px; text-align: center;
  }
  .card--back .wordmark {
    position: absolute; left: 0; right: 0; top: 150px;
    color: var(--brand-blue); font-size: 36px;
  }
  .contact { position: absolute; left: 0; right: 0; top: 358px; }
  .owner-name {
    color: var(--brand-blue); font-weight: 700; font-size: 22px; letter-spacing: 0.2px;
  }
  .owner-role { font-size: 17px; margin-top: 3px; color: #333; }
  .rule { width: 72px; height: 1px; background: var(--rule); margin: 14px auto; }
  .phone, .email { font-size: 16px; line-height: 22px; }
  .services { font-size: 15px; line-height: 27px; }
  .services .dot {
    display: inline-block; width: 9px; height: 9px; border-radius: 50%;
    background: var(--brand-blue); margin: 0 4px 2px; vertical-align: middle;
  }
</style>
</head>
<body>
<main class="stage">
  <section class="card card--front">
    <div class="pattern" role="img" aria-label="Faint spark burst background pattern"></div>
    <p class="wordmark">Raven Forge<br>and Mend</p>
  </section>

  <section class="card card--back">
    <p class="wordmark">Raven Forge<br>and Mend</p>
    <div class="contact">
      <p class="owner-name">DALTON WHITCOMB</p>
      <p class="owner-role">OWNER</p>
      <div class="rule"></div>
      <p class="phone">208-417-3826</p>
      <p class="email">ravenforgeandmend@mailbay.net</p>
      <div class="rule"></div>
      <p class="services">FABRICATION<span class="dot"></span>MOBILE WELDING<br>SEMI REPAIR<span class="dot"></span>PIPE FENCE</p>
    </div>
  </section>
</main>
</body>
</html>
```